Stationary Set Rebrand for Brennick

We are a Canadian Distribution and Service Company that was established in 1969. Over the past 5 decades we have expanded our business and have warehouses across Canada. We specialize in adhesive tapes, adhesives, films, safety, warehouse, shipping, janitorial and packaging supplies.

We have updated our logo design and would like a new corporate branding identity that includes a new fresh Stationary Set (Business Cards, Letterhead, Letterhead MS Word, Envelope, Presentation Folders, Email Signatures, Notepad Covers, etc.)

Target Market(s)

Industrial Business Sector

Font styles to use
Sans Serif

Colors
0054AA
0677BA
7BADD7
CADEEF
E8F1F8
0094D4
00A9DD
6FCCEA
C7EBF8
E9F6FB
00AB8E
00BBA5
67D7C9
C6EFE9
E9F9F6
EB3D1F
EC4F4E
F09395
F8D3D4
FCEDEE

Requirements
Should not have
• Colors not too light, darker colours preferred

```html
<!DOCTYPE html>
<html lang="en">
<head>
<meta charset="utf-8">
<title>Brennick Stationery Set</title>
<link rel="stylesheet" href="https://fonts.googleapis.com/css2?family=Montserrat:wght@400;500;600;700;800&family=Oswald:wght@500&display=swap">
<style>
:root{
  --ink:#1c1c1e;
  --red:#d71f26;
  --paper:#ffffff;
  --backdrop:#e1e2e4;
  --stage:#ededee;
  --rule:#c9c9cc;
  --muted:#5a5a5e;
  --window:#e7e7e9;
  --silver:#cfcfd2;
}
*{margin:0;padding:0;box-sizing:border-box}
html,body{width:1039px;height:1200px;overflow:hidden}
body{position:relative;background:var(--backdrop);font-family:"Montserrat",sans-serif;color:var(--ink)}
.stage{position:absolute;left:0;top:818px;width:1039px;height:382px;background:linear-gradient(180deg,#d6d6d8 0%,var(--stage) 45%,#f4f4f5 100%)}
.piece{position:absolute;background:var(--paper);box-shadow:0 3px 8px rgba(0,0,0,.18);overflow:hidden}
.band{position:absolute;left:0;right:0;bottom:0;height:6px;background:var(--paper)}
.band::before,.band::after{content:"";position:absolute;top:0;bottom:0}
.band::before{left:0;width:50%;background:var(--ink);clip-path:polygon(0 0,100% 0,calc(100% - 6px) 100%,0 100%)}
.band::after{left:calc(50% + 2px);right:0;background:var(--red);clip-path:polygon(6px 0,100% 0,100% 100%,0 100%)}
.band.thin{height:4px}
.logo{display:inline-flex;align-items:center;gap:.18em;font-weight:800;letter-spacing:-.02em;line-height:1;white-space:nowrap}
.logo .mark{width:.32em;height:.32em;background:var(--red);display:inline-block}
.logo.light{color:var(--paper)}
.logo.silver{color:var(--silver)}
.contact{list-style:none}
.contact li{display:flex;align-items:center;gap:.5em}
.ico{width:.9em;height:.9em;fill:var(--red);flex:none}

/* business card front */
.card-front{left:61px;top:78px;width:268px;height:157px;border-radius:7px}
.card-front .logo{position:absolute;left:0;right:0;top:18px;justify-content:center;font-size:34px}
.card-front .who{position:absolute;right:140px;top:81px;text-align:right}
.card-front .who .name{font-size:10px;font-weight:800}
.card-front .who .role{font-size:7px;color:var(--red);margin-top:3px}
.card-front .divider{position:absolute;left:138px;top:75px;width:1px;height:38px;background:var(--red)}
.card-front .contact{position:absolute;left:146px;top:73px;font-size:7.3px;line-height:10.4px}
.card-front .address{position:absolute;left:0;right:0;top:127px;text-align:center;font-size:7.3px}

/* business card back */
.card-back{left:61px;top:274px;width:268px;height:157px;border-radius:7px;background:var(--ink)}
.card-back .logo{position:absolute;left:0;right:0;top:58px;justify-content:center;font-size:42px}

/* letterhead */
.letterhead{left:348px;top:77px;width:248px;height:353px}
.letterhead .logo{position:absolute;left:21px;top:23px;font-size:17px}
.letterhead .head-contact{position:absolute;left:170px;top:16px;padding-left:4px;border-left:.6px solid var(--red);font-size:4.2px;line-height:6.3px}
.letterhead .head-contact .ico{width:4px;height:4px}
.letterhead .head-contact li{gap:2px}
.letterhead .greet{position:absolute;left:21px;top:79px}
.letterhead .greet b{display:block;font-size:5px;font-weight:700}
.letterhead .greet span{display:block;font-size:3.4px;font-weight:600;margin-top:1.5px}
.letterhead .date{position:absolute;right:21px;top:86px;font-size:3.6px;color:var(--muted)}
.letterhead .body{position:absolute;left:21px;right:21px;top:104px;font-size:3.4px;line-height:6px;color:var(--muted);text-align:justify}
.letterhead .body p{margin-bottom:6px}
.letterhead .signature{position:absolute;left:21px;top:318px;width:54px;height:14px;background:linear-gradient(90deg,#e9e9ec,#f6f6f7)}
.letterhead .signer{position:absolute;left:21px;top:338px}
.letterhead .signer b{display:block;font-size:4.6px;font-weight:700}
.letterhead .signer span{display:block;font-size:3.4px;margin-top:1.5px}
.letterhead .band{height:5px}

/* envelope */
.envelope-back{left:619px;top:77px;width:356px;height:172px}
.envelope-back svg{position:absolute;left:0;top:0}
.envelope-back .logo{position:absolute;left:0;right:0;top:20px;justify-content:center;font-size:17px}
.envelope-front{left:619px;top:259px;width:356px;height:172px}
.envelope-front .logo{position:absolute;left:23px;top:17px;font-size:20px}
.envelope-front .address{position:absolute;left:23px;top:43px;font-size:5px;line-height:7px}
.envelope-front .window{position:absolute;left:23px;top:108px;width:122px;height:38px;border-radius:5px;background:var(--window)}

/* small card */
.card-slim{left:70px;top:500px;width:252px;height:75px;box-shadow:0 2px 6px rgba(0,0,0,.16)}
.card-slim .who{position:absolute;left:11px;top:7px}
.card-slim .who .name{font-size:7.6px;font-weight:800}
.card-slim .who .role{font-size:6px;color:var(--red);margin-top:1px}
.card-slim .contact{position:absolute;left:11px;top:29px;font-size:6.4px;line-height:9.3px}
.card-slim .logo{position:absolute;right:14px;top:9px;font-size:19px}
.card-slim .address{position:absolute;right:13px;top:48px;text-align:right;font-size:6.2px;line-height:9px}

/* compliments slip */
.slip{left:61px;top:604px;width:278px;height:143px}
.slip .logo{position:absolute;left:14px;top:20px;font-size:19px}
.slip .title{position:absolute;right:14px;top:22px;font-family:"Oswald",sans-serif;font-weight:500;color:var(--red);font-size:13px}
.slip .address{position:absolute;left:14px;top:82px;font-size:5.8px;line-height:8.5px}
.slip .contact{position:absolute;left:14px;top:99px;font-size:5.8px;line-height:8.6px}
.slip .contact .ico{width:5px;height:5px}

/* notebook cover */
.notebook{position:absolute;left:360px;top:494px;width:203px;height:274px}
.notebook .cover{position:absolute;left:9px;top:0;width:194px;height:274px;background:var(--ink);border-radius:2px;box-shadow:0 3px 8px rgba(0,0,0,.25)}
.notebook .spiral{position:absolute;left:0;top:4px;width:22px;height:266px;background:repeating-linear-gradient(180deg,transparent 0 2px,#8d8d92 2px 3.6px,transparent 3.6px 5.8px)}
.notebook .logo{position:absolute;left:0;right:0;top:121px;justify-content:center;font-size:29px}

/* open notebook */
.pad{position:absolute;left:589px;top:492px;width:389px;height:273px}
.pad .page{position:absolute;top:0;width:194px;height:273px;background:var(--paper);box-shadow:0 3px 8px rgba(0,0,0,.15);overflow:hidden}
.pad .page.left{left:0}
.pad .page.right{left:195px}
.pad .logo{position:absolute;left:18px;top:15px;font-size:13px}
.pad .date{position:absolute;right:18px;top:34px;font-size:3.6px;color:var(--muted)}
.pad .lines{position:absolute;left:18px;right:18px;top:47px;height:198px;background:repeating-linear-gradient(180deg,transparent 0 10.4px,var(--rule) 10.4px 11px)}
.pad .rings{position:absolute;left:187px;top:4px;width:16px;height:262px;background:repeating-linear-gradient(180deg,transparent 0 6px,#8d8d92 6px 8px,transparent 8px 12px)}

/* presentation folders */
.folder-outside{position:absolute;left:50px;top:862px;width:420px;height:296px;box-shadow:0 6px 16px rgba(0,0,0,.22)}
.folder-outside .back{position:absolute;left:0;top:0;width:210px;height:296px;background:var(--ink)}
.folder-outside .front{position:absolute;left:210px;top:0;width:210px;height:296px;background:linear-gradient(90deg,#e4e4e6,var(--paper) 30%)}
.folder-outside .back .logo{position:absolute;left:0;right:0;top:112px;justify-content:center;font-size:31px}
.folder-outside .back .foot{position:absolute;left:18px;right:18px;bottom:20px;padding-top:4px;border-top:.8px solid var(--red);color:var(--paper);font-size:5px;line-height:8px}
.folder-outside .front .logo{position:absolute;left:0;right:0;top:100px;justify-content:center;font-size:31px}
.folder-outside .front .web{position:absolute;right:22px;bottom:22px;font-size:6.4px}
.folder-inside{position:absolute;left:560px;top:862px;width:430px;height:296px;box-shadow:0 6px 16px rgba(0,0,0,.22)}
.folder-inside .panel{position:absolute;top:0;width:215px;height:296px;background:linear-gradient(180deg,#e9e9eb,var(--paper))}
.folder-inside .panel.left{left:0}
.folder-inside .panel.right{left:215px;border-left:1px solid #d4d4d6}
.folder-inside .pocket{position:absolute;left:0;right:0;bottom:0;height:98px;background:var(--ink)}
.folder-inside .pocket .logo{position:absolute;left:0;right:0;top:34px;justify-content:center;font-size:22px}
.folder-inside .mini-card{position:absolute;left:72px;top:-22px;width:82px;height:48px;background:var(--paper);box-shadow:0 1px 3px rgba(0,0,0,.3);padding:5px}
.folder-inside .mini-card .logo{font-size:9px;justify-content:center;display:flex}
.folder-inside .mini-card .row{display:flex;justify-content:space-between;margin-top:5px;font-size:2.8px;line-height:4px}
.folder-inside .mini-card .row .role{color:var(--red)}
.folder-inside .mini-card .addr{text-align:center;font-size:2.6px;margin-top:4px}
</style>
</head>
<body>
<svg width="0" height="0" style="position:absolute">
  <defs>
    <symbol id="i-phone" viewBox="0 0 10 10"><path d="M1 3.2C1 2 2 1 3.2 1h3.6C8 1 9 2 9 3.2V4H6.8V3.2H3.2V4H1zM2 5h6l1 4H1z"/></symbol>
    <symbol id="i-mobile" viewBox="0 0 10 10"><path d="M3 .5h4a1 1 0 0 1 1 1v7a1 1 0 0 1-1 1H3a1 1 0 0 1-1-1v-7a1 1 0 0 1 1-1zm.2 1.2v6.1h3.6V1.7z"/></symbol>
    <symbol id="i-mail" viewBox="0 0 10 10"><path d="M.5 2h9v6h-9zM1.4 2.8 5 5.4l3.6-2.6z"/></symbol>
    <symbol id="i-web" viewBox="0 0 10 10"><path d="M5 .5a4.5 4.5 0 1 1 0 9 4.5 4.5 0 0 1 0-9zm0 1.2a3.3 3.3 0 1 0 0 6.6 3.3 3.3 0 0 0 0-6.6zM3.2 3.6h3.6v2.8H3.2z"/></symbol>
  </defs>
</svg>

<!-- business card front -->
<section class="piece card-front">
  <div class="logo">Brennick<span class="mark"></span></div>
  <div class="who"><div class="name">MARTIN CALLOWAY</div><div class="role">Founder &amp; CEO</div></div>
  <div class="divider"></div>
  <ul class="contact">
    <li><svg class="ico"><use href="#i-phone"/></svg>555-014-7720</li>
    <li><svg class="ico"><use href="#i-mobile"/></svg>555-014-7720</li>
    <li><svg class="ico"><use href="#i-mail"/></svg>info@brennicksales.com</li>
    <li><svg class="ico"><use href="#i-web"/></svg>www.brennicksales.com</li>
  </ul>
  <div class="address">27-810 Cedar Ridge Dr, Guelph, ON N1K 4T2</div>
  <div class="band"></div>
</section>

<!-- business card back -->
<section class="piece card-back">
  <div class="logo silver">Brennick<span class="mark"></span></div>
</section>

<!-- letterhead -->
<section class="piece letterhead">
  <div class="logo">Brennick<span class="mark"></span></div>
  <ul class="contact head-contact">
    <li>27-810 Cedar Ridge Dr</li>
    <li>Guelph, ON N1K 4T2</li>
    <li><svg class="ico"><use href="#i-phone"/></svg>555-014-7720</li>
    <li><svg class="ico"><use href="#i-mail"/></svg>info@brennicksales.com</li>
    <li><svg class="ico"><use href="#i-web"/></svg>www.brennicksales.com</li>
  </ul>
  <div class="greet"><b>Dear. Mrs Laura Bennett</b><span>Chief Director</span></div>
  <div class="date">Date: 16-October-2025</div>
  <div class="body">
    <p>Thank you for your continued partnership with our team. We supply adhesive tapes, films, safety products and packaging materials to industrial clients across the country, and we are pleased to share an update on our service. Our warehouses now carry a wider range of stock, which lets us ship most orders on the same day. Each shipment is checked by our staff before it leaves the dock, and every client has a direct contact for questions about pricing, delivery and product fit. We value your trust and look forward to supporting your operations in the months ahead.</p>
    <p>Please find enclosed our updated catalogue and price list for the coming season. New items include stretch films, carton sealing tapes and janitorial supplies in bulk sizes. If you would like samples or a site visit, our account managers are happy to arrange one at a time that suits your schedule. Volume discounts remain in place for all standing orders placed before the end of the quarter.</p>
    <p>Thank you again for choosing us. Do not hesitate to reach out if there is anything we can do to help your team work better.</p>
  </div>
  <div class="signature" role="img" aria-label="Handwritten signature"></div>
  <div class="signer"><b>Daniel Reeve</b><span>Chief Director</span></div>
  <div class="band"></div>
</section>

<!-- envelope flap side -->
<section class="piece envelope-back">
  <svg width="356" height="172" viewBox="0 0 356 172" aria-hidden="true">
    <path d="M0 0H356L344 34Q339 46 325 48L192 61Q178 63 164 61L31 48Q17 46 12 34Z" fill="var(--ink)"/>
  </svg>
  <div class="logo light">Brennick<span class="mark"></span></div>
</section>

<!-- envelope address side -->
<section class="piece envelope-front">
  <div class="logo">Brennick<span class="mark"></span></div>
  <div class="address">27-810 Cedar Ridge Dr<br>Guelph, ON N1K 4T2</div>
  <div class="window"></div>
  <div class="band"></div>
</section>

<!-- slim business card -->
<section class="piece card-slim">
  <div class="who"><div class="name">MARTIN CALLOWAY</div><div class="role">CEO &amp; Founder</div></div>
  <ul class="contact">
    <li><svg class="ico"><use href="#i-phone"/></svg>555-014-7720</li>
    <li><svg class="ico"><use href="#i-mobile"/></svg>555-014-7720</li>
    <li><svg class="ico"><use href="#i-mail"/></svg>info@brennicksales.com</li>
    <li><svg class="ico"><use href="#i-web"/></svg>www.brennicksales.com</li>
  </ul>
  <div class="logo">Brennick<span class="mark"></span></div>
  <div class="address">27-810 Cedar Ridge Dr<br>Guelph, ON N1K 4T2</div>
  <div class="band thin"></div>
</section>

<!-- compliments slip -->
<section class="piece slip">
  <div class="logo">Brennick<span class="mark"></span></div>
  <div class="title">With Compliments</div>
  <div class="address">27-810 Cedar Ridge Dr<br>Guelph, ON N1K 4T2</div>
  <ul class="contact">
    <li><svg class="ico"><use href="#i-phone"/></svg>555-014-7720</li>
    <li><svg class="ico"><use href="#i-mail"/></svg>info@brennicksales.com</li>
    <li><svg class="ico"><use href="#i-web"/></svg>www.brennicksales.com</li>
  </ul>
  <div class="band"></div>
</section>

<!-- notebook cover -->
<section class="notebook">
  <div class="cover"><div class="logo light">Brennick<span class="mark"></span></div></div>
  <div class="spiral"></div>
</section>

<!-- notepad pages -->
<section class="pad">
  <div class="page left">
    <div class="logo">Brennick<span class="mark"></span></div>
    <div class="date">Date:......./......./.........</div>
    <div class="lines"></div>
    <div class="band thin"></div>
  </div>
  <div class="page right">
    <div class="logo">Brennick<span class="mark"></span></div>
    <div class="date">Date:......./......./.........</div>
    <div class="lines"></div>
    <div class="band thin"></div>
  </div>
  <div class="rings"></div>
</section>

<div class="stage"></div>

<!-- presentation folder outside -->
<section class="folder-outside">
  <div class="back">
    <div class="logo light">Brennick<span class="mark"></span></div>
    <div class="foot">27-810 Cedar Ridge Dr, Guelph, ON N1K 4T2<br>555-014-7720 &nbsp;•&nbsp; info@brennicksales.com &nbsp;•&nbsp; www.brennicksales.com</div>
  </div>
  <div class="front">
    <div class="logo">Brennick<span class="mark"></span></div>
    <div class="web">www.brennicksales.com</div>
    <div class="band thin"></div>
  </div>
</section>

<!-- presentation folder inside -->
<section class="folder-inside">
  <div class="panel left">
    <div class="pocket"><div class="logo light">Brennick<span class="mark"></span></div></div>
  </div>
  <div class="panel right">
    <div class="pocket">
      <div class="mini-card">
        <div class="logo">Brennick<span class="mark"></span></div>
        <div class="row"><div><b>MARTIN CALLOWAY</b><br><span class="role">Founder &amp; CEO</span></div><div>555-014-7720<br>info@brennicksales.com</div></div>
        <div class="addr">27-810 Cedar Ridge Dr, Guelph, ON N1K 4T2</div>
      </div>
    </div>
  </div>
</section>
</body>
</html>
```